Sophisticated, clean website reflecting my feminine, playful side to sell my abstract art,

I need a website no more than 3 pages to showcase my paintings, a little about me and some contact info. I do abstracts so looking for something a little edgy, yet feminine and current.
Updates

Hi there, These are some artists websites that I Iike: Marnelvoss.com (I like how airy it is) peterwallombry.com garethpolvens.com (I like how it scrolls) I'll need a place for a photo ( a headshot-i do not have it yet so I'll need to be able to upload that later) as well as an area for my bio. Also, it's important that I will be able to upload any new photos and descriptions easily so it should be user friendly. Lastly, I like in a sunny place so would like to have this seem upbeat and playful as that is how i like to paint. thanks-I'm trying to upload my photos now -

Target Market(s)

ppl ages 35-70 who want large scale art for their homes

Industry/Entity Type

art

Coding

Coded - Design and coding required

Number of Pages Required

3 page

Colors

Designer to choose colors to be used in the design.

Requirements
Must have
• photos of my art, a place for my bio, be easy to reach me. tasteful-nothing too "in your face" -my clients are pretty high end and organized. They like clean lines
Nice to have
• sophisticated background, muted tones in the back-similar clean font throughout-no cursive
Should not have
• too many dark areas. Too many blocks of color. Too serious.

```html
<!DOCTYPE html>
<html lang="en">
<head>
<meta charset="utf-8">
<title>Lena Marwood Art</title>
<link href="https://fonts.googleapis.com/css2?family=Cambo&display=swap" rel="stylesheet">
<style>
:root{
  --ink:#2b2b2b;
  --text:#444;
  --accent:#f07444;
  --header-bg:#f4f4f4;
  --blush:#fdf3f3;
  --white:#fff;
}
*{box-sizing:border-box;margin:0;padding:0}
html,body{width:1200px;height:3415px;overflow:hidden}
body{position:relative;background:var(--white);font-family:"Cambo",Georgia,serif;color:var(--text)}
.abs{position:absolute}
.site-header{left:0;top:0;width:1200px;height:97px;background:var(--header-bg)}
.brand{left:75px;top:22px;font-size:44px;color:var(--ink);letter-spacing:1px}
.menu-icon{left:1097px;top:34px}
h1,h2{font-weight:400;color:var(--ink);letter-spacing:1px}
.hero-title{left:75px;top:240px;font-size:58px;line-height:61px}
.hero-title span{color:var(--accent)}
.body-text{font-size:17px;line-height:29px}
.body-text.loose{line-height:35px}
.btn{display:flex;align-items:center;justify-content:center;border:1px solid var(--accent);color:var(--accent);font-size:16px;letter-spacing:.5px;height:54px}
.hero-frame{left:587px;top:155px;width:540px;height:473px;background:var(--accent)}
.art{box-shadow:0 6px 14px rgba(0,0,0,.15)}
.blush-bg{left:0;top:783px;width:1200px;height:1204px}
.card{background:var(--white);box-shadow:0 2px 10px rgba(0,0,0,.08)}
.section-title{font-size:46px}
.contact-band{left:0;top:2726px;width:1200px;height:434px;background:linear-gradient(90deg,#e7c9b8 0%,#efc6a0 30%,#3aa37a 55%,#2f6bb0 75%,#e8a23a 100%)}
.contact-box{left:75px;top:2802px;width:513px;height:283px;background:rgba(255,255,255,.85);text-align:center}
.footer-name{left:0;top:3222px;width:1200px;text-align:center;font-size:42px;color:#444;letter-spacing:1px}
.copyright{left:0;top:3286px;width:1200px;text-align:center;font-size:17px}
.socials{left:480px;top:3322px;width:240px;display:flex;justify-content:space-between}
.socials span{width:26px;height:26px;border-radius:50%;background:#333;display:block}
</style>
</head>
<body>
<header class="abs site-header">
  <div class="abs brand">Lena Marwood Art</div>
  <svg class="abs menu-icon" width="30" height="30" viewBox="0 0 30 30" aria-label="Menu"><rect x="4" y="2" width="26" height="4" fill="#333"/><rect x="0" y="10" width="30" height="4" fill="#333"/><rect x="4" y="18" width="26" height="4" fill="#333"/><rect x="0" y="26" width="30" height="4" fill="#333"/></svg>
</header>

<section class="hero">
  <h1 class="abs hero-title">Welcome to<br>Lena Marwood<br><span>Art</span></h1>
  <p class="abs body-text" style="left:75px;top:434px;width:490px">Sed ut perspiciatis unde omnis iste natus error sit voluptatem accusantium doloremque laudantium, totam rem aperiam, eaque ipsa quae.</p>
  <a class="abs btn" style="left:75px;top:549px;width:182px">View My Painting</a>
  <svg class="abs" style="left:75px;top:674px" width="90" height="20" aria-label="Previous and next"><path d="M2 10h28M10 3 2 10l8 7" stroke="#444" stroke-width="4" fill="none"/><path d="M60 10h28M80 3l8 7-8 7" stroke="var(--accent)" stroke-width="4" fill="none"/></svg>
  <div class="abs hero-frame"></div>
  <div class="abs art" role="img" aria-label="Featured abstract painting in green, teal and charcoal strokes" style="left:601px;top:170px;width:512px;height:527px;background:linear-gradient(135deg,#d9d6cf,#4f9a72 40%,#2a4a40 60%,#c9c3b4)"></div>
</section>

<svg class="abs blush-bg" viewBox="0 0 1200 1204" preserveAspectRatio="none"><polygon points="1200,0 1200,1204 0,1204" fill="var(--blush)"/></svg>

<section class="abs card" style="left:0;top:783px;width:884px;height:592px">
  <h2 class="abs section-title" style="left:75px;top:108px">About Me</h2>
  <p class="abs body-text loose" style="left:75px;top:180px;width:600px">Sed ut perspiciatis unde omnis iste natus error sit voluptatem accusantium doloremque laudantium, totam rem aperiam, eaque ipsa quae ab illo inventore veritatis et quasi architecto beatae vitae dicta sunt explicabo. Nemo enim ipsam voluptatem quia voluptas sit aspernatur aut odit aut fugit, sed quia consequuntur magni dolores eos qui ratione voluptatem sequi nesciunt.</p>
  <a class="abs btn" style="left:75px;top:420px;width:182px">More About Me</a>
</section>
<div class="abs" role="img" aria-label="Photo of the artist at her easel holding paintbrushes" style="left:704px;top:840px;width:436px;height:478px;background:linear-gradient(120deg,#e8e4de,#cfc6b6 50%,#8a9bb0)"></div>

<section class="gallery">
  <h2 class="abs section-title" style="left:75px;top:1434px">My Painting Gallery</h2>
  <svg class="abs" style="left:1038px;top:1456px" width="90" height="20" aria-label="Previous and next"><path d="M2 10h28M10 3 2 10l8 7" stroke="#444" stroke-width="4" fill="none"/><path d="M60 10h28M80 3l8 7-8 7" stroke="var(--accent)" stroke-width="4" fill="none"/></svg>
  <div class="abs art" role="img" aria-label="Abstract painting of violet floral shapes" style="left:75px;top:1539px;width:241px;height:326px;background:linear-gradient(160deg,#d8d2d6,#6e4f7e 50%,#c9c0c6)"></div>
  <div class="abs art" role="img" aria-label="Abstract painting in ochre, red and navy swirls" style="left:345px;top:1585px;width:242px;height:325px;background:linear-gradient(160deg,#c8902a,#a8621c 50%,#d4a23c)"></div>
  <div class="abs art" role="img" aria-label="Abstract painting with a teal field beside a pale stripe" style="left:615px;top:1539px;width:242px;height:326px;background:linear-gradient(90deg,#9aa3b3 0%,#d8cfc2 30%,#136e66 40%,#1b8a7e 100%)"></div>
  <div class="abs art" role="img" aria-label="Abstract painting with blue and yellow gestural marks" style="left:885px;top:1585px;width:242px;height:325px;background:linear-gradient(160deg,#dfe2ea,#8fa6d8 40%,#e4d07a 60%,#d7d4cc)"></div>
</section>

<section class="abs card" style="left:332px;top:2056px;width:868px;height:593px">
  <h2 class="abs section-title" style="left:203px;top:110px">Abstracts</h2>
  <p class="abs body-text loose" style="left:203px;top:180px;width:610px">Sed ut perspiciatis unde omnis iste natus error sit voluptatem accusantium doloremque laudantium, totam rem aperiam, eaque ipsa quae ab illo inventore veritatis et quasi architecto beatae vitae dicta sunt explicabo. Nemo enim ipsam voluptatem quia voluptas sit aspernatur aut odit aut fugit, sed quia consequuntur magni dolores eos qui ratione voluptatem sequi nesciunt.</p>
  <a class="abs btn" style="left:203px;top:419px;width:201px">View Our Paintings</a>
</section>
<div class="abs" role="img" aria-label="Textured abstract painting in turquoise and golden yellow" style="left:76px;top:2113px;width:435px;height:477px;background:linear-gradient(170deg,#2aa3b0 0%,#58b6b0 30%,#f0b21a 55%,#e8a412 100%)"></div>

<section>
  <div class="abs contact-band" role="img" aria-label="Painted landscape of colourful trees under a warm sky"></div>
  <div class="abs contact-box">
    <h2 class="section-title" style="margin-top:28px">Contact Info</h2>
    <p style="font-size:24px;margin-top:12px;color:#333">1-555-018-2740</p>
    <p style="font-size:24px;margin-top:6px;color:#333">hello@lenamarwood.com</p>
    <a class="btn" style="width:201px;margin:34px auto 0">Contact Us</a>
  </div>
</section>

<footer>
  <div class="abs footer-name">Lena Marwood Art</div>
  <p class="abs copyright">Copyright © 2022 Ardent Studio · All Rights Reserved.</p>
  <div class="abs socials" aria-label="Social links"><span></span><span></span><span></span><span></span><span></span></div>
</footer>
</body>
</html>
```